Vantrel System Web Page Design

This project is to design 6 pages of a web based medical system for clinics, hospitals, drugs suppliers, general items suppliers, insurance company, laboratories and patients (basically all parties which could be involved in).We want the designs of the browser, button, icon and layout are based on Zeltor, which is user friendly, looks professional, simple and neat but with powerful functions. We have uploaded few pictures of another system, please do not copy its design because this is not what we are looking for, the pictures are for you to know the elements should be included in our pages. Vantrel web-base system, design 6 pages1. Login PageShould include the following elements-company id with input field-login id with input field-password with input field2. Main Page (Navigation page)Should include the following elements-Appointment-Consultation-Patient-Drugs inventory -General supplies inventory -Laboratory-Suppliers-Insurance-Reports 3. Appointment PageShould include all the the elements in the respective pictures plus the followings-Daily View, Weekly View, Monthly View buttons4. Consultation PageShould include all the the elements in the respective picture5. Patient Page5.1 General information Should include all the the elements in the respective picture5.2 medical history/lab reportsShould include all the the elements in the respective picture plus the followings-Notify patient button-Share report button.
Updated on 28 Nov:
Please stop using Harbor Suite in your designs which is not the name of our system. We have just rename our system to Vantrel, please take note.
We need the system to look professional not playful, do not use too many colors and playful icons.

```html
<!DOCTYPE html>
<html lang="en">
<head>
<meta charset="utf-8">
<title>Vantrel — Allergy</title>
<link href="https://fonts.googleapis.com/css2?family=Roboto:wght@300;400;500;700&display=swap" rel="stylesheet">
<style>
:root{
  --blue:#1a73e8;
  --blue-soft:#cfe3fb;
  --blue-line:#d6e6fa;
  --blue-text:#c3dbf8;
  --ink:#222;
  --ink-soft:#3a3a3a;
  --muted:#d4d4d4;
  --muted-bold:#dadada;
  --panel-line:#f0f0f0;
  --side-bg:#f7f7f7;
  --rule:#ececec;
}
*{box-sizing:border-box;margin:0;padding:0}
html,body{width:1200px;height:986px;overflow:hidden;background:#fff;font-family:"Roboto",Arial,sans-serif}
.app{position:relative;width:1200px;height:986px;overflow:hidden}
.abs{position:absolute}
.topbar{left:0;top:0;width:1200px;height:82px;background:#fafafa;border-bottom:1px solid #c9c9c9}
.brand{left:32px;top:22px;font-size:30px;font-weight:400;color:var(--blue);display:flex;align-items:center;gap:8px}
.brand-dot{width:12px;height:12px;border-radius:50%;background:var(--blue)}
.avatar{left:957px;top:13px;width:58px;height:58px;border-radius:50%;background:linear-gradient(160deg,#cdd6e0,#7d8ea3);border:2px solid #e3e3e3}
.user{left:1029px;top:32px;font-size:16px;color:var(--ink)}
.user-caret{left:1146px;top:34px}
.sidebar{left:0;top:82px;width:210px;height:904px;background:var(--side-bg);border-right:1px solid var(--rule)}
.nav{position:absolute;left:32px;font-size:15px;color:var(--muted);font-weight:300}
.nav.major{font-weight:700;color:var(--muted-bold)}
.nav-active{left:0;top:190px;width:210px;height:37px;background:var(--blue-soft)}
.nav.active{color:#fff;font-weight:300}
.sep{position:absolute;left:0;width:210px;height:1px;background:#eeeeee}
.card{border:1px solid var(--panel-line);border-radius:4px;background:#fff}
.info{font-size:11.5px;color:var(--muted);font-weight:300;line-height:1}
.info span{position:absolute;left:0;white-space:nowrap}
.scroll{width:6px;border-radius:3px;background:#e4e4e4}
.btn{border:2px solid var(--blue-line);border-radius:4px;color:var(--blue-text);font-size:14px;font-weight:300;display:flex;align-items:center;justify-content:center;background:#fff}
.btn.fill{background:var(--blue-soft);border-color:var(--blue-soft);color:#fff}
.btn.ghost{border-color:#f3f3f3;color:#f0f0f0}
.rule-h{height:1px;background:var(--rule)}
.rule-v{width:1px;background:var(--rule)}
.band{background:var(--blue-soft);color:#fff;font-size:12px;font-weight:500;display:flex;align-items:center;padding-left:15px;border-radius:3px 3px 0 0}
.rx{position:absolute;left:0;width:433px;height:47px;font-size:11.5px;font-weight:300}
.rx.alt{background:#f7f7f7}
.rx .drug{position:absolute;left:15px;top:6px;color:var(--blue-text)}
.rx .col{position:absolute;top:23px;color:var(--muted)}
.modal{left:399px;top:229px;width:402px;height:304px;background:#fff;border-radius:3px;box-shadow:0 10px 30px rgba(0,0,0,.16)}
.note{position:absolute;left:79px;font-size:16px;font-weight:300;color:var(--ink-soft);white-space:nowrap}
.note b{font-weight:300;position:absolute}
</style>
</head>
<body>
<div class="app">

  <header class="abs topbar">
    <div class="abs brand">Vantrel <span class="brand-dot"></span></div>
    <div class="abs avatar" role="img" aria-label="User profile photo"></div>
    <div class="abs user">Aldo Renner</div>
    <svg class="abs user-caret" width="16" height="10" viewBox="0 0 16 10"><path d="M2 2l6 6 6-6" fill="none" stroke="var(--blue)" stroke-width="2.5" stroke-linecap="round"/></svg>
  </header>

  <nav class="abs sidebar">
    <div class="nav major" style="top:31px">Appointments</div>
    <div class="sep" style="top:61px"></div>
    <div class="nav major" style="top:76px">Consultation</div>
    <div class="abs nav-active" style="top:108px"></div>
    <div class="nav active" style="top:118px">Allergy</div>
    <div class="nav" style="top:158px">Medical His.</div>
    <div class="nav" style="top:197px">Immunization</div>
    <div class="nav" style="top:235px">Glucose Data H</div>
    <div class="nav" style="top:274px">BP Data G</div>
    <div class="nav" style="top:313px">Laboratory</div>
    <div class="nav" style="top:351px">Image,Doc</div>
    <div class="nav" style="top:391px">Othhers</div>
    <div class="sep" style="top:425px"></div>
    <div class="nav major" style="top:432px">Patient</div>
    <div class="sep" style="top:456px"></div>
    <div class="nav major" style="top:463px">Drugs inventory</div>
    <div class="sep" style="top:488px"></div>
    <div class="nav major" style="top:495px;line-height:18px">General supplies<br>inventory</div>
    <div class="sep" style="top:537px"></div>
    <div class="nav major" style="top:545px">Laboratory</div>
    <div class="sep" style="top:569px"></div>
    <div class="nav major" style="top:576px">Suppliers</div>
    <div class="sep" style="top:600px"></div>
    <div class="nav major" style="top:607px">Insurance</div>
    <div class="sep" style="top:631px"></div>
    <div class="nav major" style="top:639px">Reports</div>
    <div class="sep" style="top:663px"></div>
  </nav>

  <main>
    <div class="abs rule-v" style="left:690px;top:82px;height:727px"></div>

    <section class="abs card" style="left:235px;top:112px;width:432px;height:154px">
      <div class="abs info" style="left:15px;top:15px">
        <span style="top:0">000001</span>
        <span style="top:18px">A000001(1) MALE (01 Jan,1988, 22Yr)</span>
        <span style="top:35px">HO WAI LUN</span>
        <span style="top:54px">M: 61204387,&nbsp;&nbsp;&nbsp; T: 27650914</span>
        <span style="top:73px">28 Jan, 2010</span>
      </div>
      <div class="abs scroll" style="left:418px;top:26px;height:90px"></div>
    </section>

    <section class="abs card" style="left:714px;top:112px;width:456px;height:154px">
      <div class="abs info" style="left:15px;top:15px">
        <span style="top:0">FLAT P, 24/F</span>
        <span style="top:18px">KELMOR HOUSE</span>
        <span style="top:35px">BRISDALE</span>
      </div>
      <div class="abs scroll" style="left:442px;top:6px;height:88px"></div>
    </section>

    <div class="abs btn" style="left:238px;top:282px;width:91px;height:36px">Add</div>
    <div class="abs btn ghost" style="left:339px;top:282px;width:91px;height:36px">Edit</div>
    <div class="abs btn" style="left:716px;top:282px;width:91px;height:36px">Add</div>
    <div class="abs btn ghost" style="left:818px;top:282px;width:92px;height:36px">Edit</div>
    <div class="abs btn" style="left:918px;top:282px;width:92px;height:36px">Delete</div>

    <div class="abs rule-h" style="left:210px;top:346px;width:990px"></div>

    <div class="abs band" style="left:235px;top:374px;width:432px;height:31px">28 JUNE, 2010</div>
    <section class="abs card" style="left:235px;top:405px;width:432px;height:369px;border-radius:0 0 4px 4px">
      <div class="abs info" style="left:15px;top:20px">
        <span style="top:0">000001</span>
        <span style="top:18px">A000001(1) MALE (01 Jan,1988, 22Yr)</span>
        <span style="top:35px">HO WAI LUN</span>
        <span style="top:53px">M: 61204387,&nbsp;&nbsp;&nbsp; T: 27650914</span>
        <span style="top:72px">28 Jan, 2010</span>
      </div>
    </section>

    <div class="abs card" style="left:760px;top:381px;width:282px;height:37px"></div>
    <svg class="abs" style="left:1011px;top:394px" width="16" height="10" viewBox="0 0 16 10"><path d="M2 2l6 6 6-6" fill="none" stroke="var(--blue-text)" stroke-width="2.5" stroke-linecap="round"/></svg>
    <div class="abs btn" style="left:1053px;top:381px;width:91px;height:36px">View</div>

    <div class="abs rule-h" style="left:690px;top:454px;width:510px"></div>

    <div class="abs band" style="left:717px;top:494px;width:433px;height:31px">28 JUNE, 2010</div>
    <section class="abs card" style="left:717px;top:525px;width:433px;height:245px;border-radius:0 0 4px 4px">
      <div class="rx" style="top:14px">
        <span class="drug">PARACETAMOL 250MG</span>
        <span class="col" style="left:15px">Dos: 1</span><span class="col" style="left:82px">Feq:E6-PRN</span><span class="col" style="left:173px">Day:3</span><span class="col" style="left:238px">Quantity:12.00</span>
      </div>
      <div class="rx alt" style="top:61px">
        <span class="drug">PARACETAMOL 250MG</span>
        <span class="col" style="left:15px">Dos: 1</span><span class="col" style="left:82px">Feq:E6-PRN</span><span class="col" style="left:173px">Day:3</span><span class="col" style="left:238px">Quantity:12.00</span>
      </div>
      <div class="rx" style="top:108px">
        <span class="drug">PARACETAMOL 250MG</span>
        <span class="col" style="left:15px">Dos: 1</span><span class="col" style="left:82px">Feq:E6-PRN</span><span class="col" style="left:173px">Day:3</span><span class="col" style="left:238px">Quantity:12.00</span>
      </div>
      <div class="abs scroll" style="left:420px;top:16px;height:88px"></div>
    </section>

    <div class="abs rule-h" style="left:210px;top:809px;width:990px"></div>

    <div class="abs btn fill" style="left:257px;top:852px;width:92px;height:36px">Next</div>
    <div class="abs btn" style="left:364px;top:852px;width:110px;height:36px">Appoint</div>
    <div class="abs btn" style="left:491px;top:852px;width:110px;height:36px">Search</div>
    <div class="abs btn" style="left:618px;top:852px;width:109px;height:36px">ReCall</div>
    <div class="abs btn" style="left:742px;top:852px;width:109px;height:36px">Write</div>
    <div class="abs btn" style="left:865px;top:852px;width:90px;height:36px">Bill</div>
    <div class="abs btn" style="left:969px;top:851px;width:109px;height:36px">Document X</div>
    <div class="abs btn" style="left:257px;top:901px;width:89px;height:36px">Print</div>
    <div class="abs btn" style="left:364px;top:901px;width:110px;height:36px">Main</div>

    <div class="abs modal" role="dialog" aria-label="Patient summary">
      <div class="note" style="top:78px">[28/06/2018]<b style="left:112px">BP: 161/102 P:83</b></div>
      <div class="note" style="top:109px">[ALLERGY]<b style="left:89px">Antibiotics</b></div>
      <div class="note" style="top:140px">ASPIRIN<b style="left:68px">100MG</b></div>
      <div class="note" style="top:171px">ASPIRIN<b style="left:68px">300MG</b></div>
      <div class="note" style="top:202px">[MEDICAL HISTORY]<b style="left:156px">Hypertension</b></div>
    </div>
  </main>

</div>
</body>
</html>
```